business card design for a plumbing contractor

i need a double business card for a plumbing business, our initial service is residential Sewer Drain Cleaning.

Target Market(s)

other plumbing Business

Industry/Entity Type

Plumbing

Contact Information for Business Card

www.PipeworksTopMark.example- 5307218394-

Font styles to use
Serif

Colors
ec1f27
0455a3

```html
<!DOCTYPE html>
<html lang="en">
<head>
<meta charset="utf-8">
<title>Pipeworks Top Mark – Business Card</title>
<link rel="stylesheet" href="https://fonts.googleapis.com/css2?family=Roboto+Condensed:wght@400;500;700&family=Roboto:wght@400;500&display=swap">
<style>
  :root {
    --backdrop: #2b2b2b;
    --brand-red: #d63a30;
    --paper: #efefef;
    --ink-white: #ffffff;
    --ink-grey: #555555;
    --ink-logo: #6f665b;
    --dot-red: #d8322a;
  }
  * { margin: 0; padding: 0; box-sizing: border-box; }
  html, body {
    width: 1200px;
    height: 960px;
    overflow: hidden;
    background: var(--backdrop);
  }
  .canvas {
    position: relative;
    width: 1200px;
    height: 960px;
  }
  .card {
    position: absolute;
    width: 600px;
    height: 343px;
    overflow: hidden;
  }
  .card-front {
    left: 322px;
    top: 108px;
    background: var(--brand-red);
    color: var(--ink-white);
    font-family: "Roboto Condensed", "Arial Narrow", sans-serif;
  }
  .card-back {
    left: 320px;
    top: 493px;
    background: var(--paper);
  }
  .contact-block {
    position: absolute;
    left: 23px;
    top: 210px;
  }
  .person-name {
    font-size: 22px;
    font-weight: 500;
    letter-spacing: 0.3px;
    line-height: 24px;
  }
  .person-role {
    font-size: 15.5px;
    font-weight: 500;
    line-height: 19px;
    margin-bottom: 13px;
  }
  .contact-line {
    font-size: 14.5px;
    line-height: 17.5px;
  }
  .front-brand {
    position: absolute;
    right: 34px;
    top: 120px;
    text-align: right;
  }
  .front-brand-square {
    display: block;
    width: 48px;
    height: 48px;
    margin: 0 0 12px auto;
    background: var(--ink-white);
  }
  .front-brand-name {
    font-size: 58px;
    font-weight: 700;
    line-height: 58px;
    color: var(--ink-white);
  }
  .brand-name {
    position: absolute;
    left: 0;
    right: 0;
    top: 148px;
    text-align: center;
    font-family: "Roboto", Arial, sans-serif;
    font-weight: 500;
    font-size: 36px;
    color: var(--ink-logo);
    letter-spacing: 0.5px;
  }
  .service-list {
    position: absolute;
    left: 0;
    right: 0;
    top: 283px;
    text-align: center;
    font-family: "Roboto", Arial, sans-serif;
    font-size: 15px;
    color: var(--ink-grey);
  }
  .service-dot {
    display: inline-block;
    width: 6px;
    height: 6px;
    border-radius: 50%;
    background: var(--dot-red);
    margin: 0 5px 2px;
    vertical-align: middle;
  }
</style>
</head>
<body>
<main class="canvas">
  <section class="card card-front">
    <div class="contact-block">
      <p class="person-name">DANA WHITFIELD</p>
      <p class="person-role">CEO/FOUNDER</p>
      <p class="contact-line">Phone : 5307218394</p>
      <p class="contact-line">Dispatcher@PipeworksTopMark.example</p>
      <p class="contact-line">www.PipeworksTopMark.example</p>
    </div>
    <div class="front-brand">
      <span class="front-brand-square"></span>
      <p class="front-brand-name">Pipeworks<br>Top Mark</p>
    </div>
  </section>

  <section class="card card-back">
    <p class="brand-name">Pipeworks Top Mark</p>
    <p class="service-list">Sewer Drain Cleaning<span class="service-dot"></span>Maintenance<span class="service-dot"></span>Trenchless Pipe Installs</p>
  </section>
</main>
</body>
</html>
```